Business Card Design For A Renovation Contractor Company

We need a business card for a new company based in Singapore, our company name is "RB Tolvane". We are a renovation contractor that builds designs into reality. We build more of F&B restaurants, retail stores and commercial offices. We work very closely with designers. The final design should communicate to our client that we are a company that you can trust, that will plan and complete your project without giving you a headache. I like my client to remember my company as "RB". The beauty of SIMPLE is important.

Industry/Entity Type

Contractor

Requirements
Nice to have
• Black or Red base

```html
<!DOCTYPE html>
<html lang="en">
<head>
<meta charset="utf-8">
<title>RB Tolvane – Business Card</title>
<link rel="stylesheet" href="https://fonts.googleapis.com/css2?family=Jost:wght@400;500;700&display=swap">
<style>
  :root {
    --backdrop: #e4e4ea;
    --card: #ffffff;
    --ink: #1c1c1c;
    --muted: #3a3a3a;
    --red: #e21b23;
    --faint: #f1eeee;
  }
  * { box-sizing: border-box; margin: 0; padding: 0; }
  html, body { width: 1200px; height: 987px; overflow: hidden; }
  body {
    background: var(--backdrop);
    font-family: "Jost", "Century Gothic", sans-serif;
    color: var(--ink);
    display: flex;
    flex-direction: column;
    align-items: center;
    justify-content: center;
    gap: 60px;
  }
  .card {
    position: relative;
    width: 700px;
    height: 400px;
    background: var(--card);
    border-radius: 28px;
    box-shadow: 0 10px 28px rgba(0,0,0,.12);
    overflow: hidden;
  }

  /* Wordmark block shared by both faces */
  .brand { position: absolute; display: flex; flex-direction: column; align-items: flex-start; }
  .brand-row { display: flex; align-items: center; gap: 18px; }
  .brand-dot {
    width: 64px; height: 64px; border-radius: 50%;
    background: var(--red);
  }
  .brand-name {
    font-weight: 400;
    font-size: 64px;
    line-height: 1;
    letter-spacing: -1px;
    color: var(--ink);
  }
  .brand-rule { width: 100%; height: 2px; background: var(--ink); margin: 8px 0 4px; }
  .brand-tagline { font-size: 27px; font-weight: 400; color: var(--ink); letter-spacing: .3px; }

  .web { font-size: 20px; letter-spacing: 5px; color: var(--muted); }
  .web .accent { color: var(--red); }

  /* Back face */
  .card-back .watermark {
    position: absolute; left: 250px; top: 40px;
    width: 300px; height: 300px; border-radius: 50%;
    border: 26px solid var(--faint);
  }
  .card-back .brand { left: 110px; top: 120px; }
  .card-back .web { position: absolute; left: 150px; top: 310px; }

  /* Front face */
  .card-front .accent-bar {
    position: absolute; left: 0; top: 34px; width: 10px; height: 40px; background: var(--red);
  }
  .contact { position: absolute; left: 44px; top: 34px; }
  .contact-name { font-weight: 700; font-size: 28px; color: var(--red); line-height: 1.1; }
  .contact-title { font-size: 18px; color: var(--muted); margin-bottom: 22px; }
  .contact-address { font-size: 18px; color: var(--muted); line-height: 1.3; margin-bottom: 18px; }
  .contact-lines { list-style: none; font-size: 18px; color: var(--muted); line-height: 1.35; }
  .contact-lines .label { color: var(--red); display: inline-block; width: 24px; }
  .card-front .web { position: absolute; left: 44px; top: 300px; font-size: 18px; }
  .card-front .brand { left: 300px; top: 200px; }
  .card-front .brand-name { font-size: 52px; }
  .card-front .brand-dot { width: 54px; height: 54px; }
  .card-front .brand-tagline { font-size: 22px; }
</style>
</head>
<body>
  <section class="card card-back" aria-label="Card back">
    <div class="watermark" aria-hidden="true"></div>
    <div class="brand">
      <div class="brand-name">RB Tolvane</div>
      <div class="brand-rule"></div>
      <div class="brand-tagline">spaces built right, on time</div>
    </div>
    <div class="web">www.rb<span class="accent">tolvane</span>.com</div>
  </section>

  <section class="card card-front" aria-label="Card front">
    <div class="accent-bar"></div>
    <div class="contact">
      <div class="contact-name">Your Name</div>
      <div class="contact-title">Title</div>
      <div class="contact-address">Door No. Street Name<br>City Name, State, Zip Code</div>
      <ul class="contact-lines">
        <li><span class="label">P:</span> 123-456-7890</li>
        <li><span class="label">C:</span> 123-456-7890</li>
        <li><span class="label">E:</span> info@rbtolvane.com</li>
      </ul>
    </div>
    <div class="web">www.rb<span class="accent">tolvane</span>.com</div>
    <div class="brand">
      <div class="brand-row">
        <div class="brand-name">RB Tolvane</div>
        <div class="brand-dot" aria-hidden="true"></div>
      </div>
      <div class="brand-rule"></div>
      <div class="brand-tagline">spaces built right, on time</div>
    </div>
  </section>
</body>
</html>
```